automotive repair and collision repair shop card

our company is called K.L Motor service we are a automotive repair company
we also do government inspections. the company information is on the cards. I would like you to use my new logo and create a new card and use the information from my old card. Good Luck!!

Industry/Entity Type

Car Repair

Contact Information for Business Card

Address: #417-18842 52 Ave, Surrey, BC V5K 8R3
Phone:(604) 555-0187
fax 604 555 0193
website www.klmotorworks.example

Font styles to use
Serif
Sans Serif

Requirements
Must have
• all the information
Should not have
• the owner and there name

```html
<!DOCTYPE html>
<html lang="en">
<head>
<meta charset="utf-8">
<title>K.L Motor service – Business Card</title>
<link href="https://fonts.googleapis.com/css2?family=Oswald:wght@300;400&family=Roboto+Condensed:wght@300;400&display=swap" rel="stylesheet">
<style>
  :root {
    --page-bg: #e9e7e4;
    --card-edge: #d9d9d9;
    --ink: #1c1c1c;
    --ink-soft: #4a4a4a;
    --mark: #6a6a6a;
  }
  * { margin: 0; padding: 0; box-sizing: border-box; }
  html, body { width: 1200px; height: 892px; overflow: hidden; }
  body {
    background: var(--page-bg);
    position: relative;
    font-family: "Roboto Condensed", sans-serif;
    color: var(--ink);
  }
  .card {
    position: absolute;
    left: 320px;
    width: 560px;
    height: 320px;
    background: linear-gradient(160deg, #ffffff 0%, #f1f1f1 100%);
    border-radius: 22px;
    box-shadow: 0 3px 0 var(--card-edge), 0 10px 24px rgba(0,0,0,0.14);
  }
  .card--front { top: 96px; }
  .card--back  { top: 476px; }

  /* front */
  .brand {
    position: absolute;
    left: 40px;
    top: 90px;
    display: flex;
    align-items: center;
    gap: 18px;
  }
  .brand__mark {
    width: 46px;
    height: 46px;
    border-radius: 50%;
    background: var(--mark);
    flex: none;
  }
  .brand__name {
    font-family: "Oswald", sans-serif;
    font-weight: 300;
    font-size: 32px;
    letter-spacing: 1px;
    line-height: 1;
  }
  .brand__tagline {
    font-family: "Oswald", sans-serif;
    font-weight: 300;
    font-size: 12px;
    color: var(--ink-soft);
    margin-top: 6px;
    letter-spacing: 0.5px;
  }
  .contact {
    position: absolute;
    left: 40px;
    bottom: 30px;
    list-style: none;
    font-size: 14px;
    line-height: 1.6;
    font-weight: 300;
  }

  /* back */
  .brand-large {
    position: absolute;
    inset: 0;
    display: flex;
    flex-direction: column;
    align-items: center;
    justify-content: center;
  }
  .brand-large__mark {
    width: 90px;
    height: 90px;
    border-radius: 50%;
    background: var(--mark);
    margin-bottom: 22px;
  }
  .brand-large__name {
    font-family: "Oswald", sans-serif;
    font-weight: 300;
    font-size: 40px;
    letter-spacing: 1.5px;
    line-height: 1;
  }
  .brand-large__tagline {
    font-family: "Oswald", sans-serif;
    font-weight: 300;
    font-size: 15px;
    color: var(--ink-soft);
    margin-top: 8px;
  }
</style>
</head>
<body>
  <section class="card card--front">
    <div class="brand">
      <div class="brand__mark"></div>
      <div>
        <div class="brand__name">K.L MOTOR SERVICE</div>
        <div class="brand__tagline">One Stop Repair Shop</div>
      </div>
    </div>
    <ul class="contact">
      <li>E : info@klmotorworks.example</li>
      <li>W : www.klmotorworks.example</li>
      <li>P : (604) 555-0187 / F : 604 555 0193</li>
      <li>A : #417-18842 52 Ave, Surrey, BC V5K 8R3</li>
    </ul>
  </section>

  <section class="card card--back">
    <div class="brand-large">
      <div class="brand-large__mark"></div>
      <div class="brand-large__name">K.L MOTOR SERVICE</div>
      <div class="brand-large__tagline">One Stop Repair Shop</div>
    </div>
  </section>
</body>
</html>
```